Print design needed to improve the layout and look of some existing documents

We need someone to take a couple of existing documents that we have and make them look much better using our existing logo and corporate colors etc. We require these to be delivered in a format that will allow our staff to edit the content as necessary via Microsoft word for conversion once finalized into a PDF. Ideally, we will also be able to use this as a newsletter template or for other documents that might be required in our business. www.corvelleadvisory.com.au
Updates

Target Market(s)

Business owners, executives, retirees

Industry/Entity Type

Financial Service

Font styles to use
Serif

Requirements
Must have
• Design that uses our existing branding and colors. It also needs to be ina form that we can edit the content / update easily. Ideally the format / layout could also be used for other documents such as short newsletters etc.
Nice to have
• Fresh, simple and crisp. Very professional looking.
Should not have
• strange fonts, weird layouts.

```html
<!DOCTYPE html>
<html lang="en">
<head>
<meta charset="utf-8">
<title>Financial Services Guide – Page 4</title>
<link href="https://fonts.googleapis.com/css2?family=Mulish:ital,wght@0,400;0,600;1,400;1,600;1,700&display=swap" rel="stylesheet">
<style>
  :root {
    --ink: #2b2b2b;
    --brand-blue: #1b9ad6;
    --brand-navy: #1d3f8f;
    --brand-green: #6ab04c;
    --bar-top: #3fa9e0;
    --bar-bottom: #6cb544;
    --paper: #ffffff;
  }
  * { margin: 0; padding: 0; box-sizing: border-box; }
  html, body { width: 848px; height: 1200px; overflow: hidden; background: var(--paper); }
  body { font-family: "Mulish", sans-serif; color: var(--ink); }
  .page { position: relative; width: 848px; height: 1200px; overflow: hidden; }
  .edge-band {
    position: absolute; top: 0; right: 0; width: 29px; height: 1200px;
    background: linear-gradient(to bottom, var(--bar-top), var(--bar-bottom));
  }
  .copy {
    position: absolute; width: 366px;
    font-style: italic; font-size: 14px; line-height: 19.3px;
    text-align: justify; hyphens: auto;
  }
  .col-left { left: 35px; }
  .col-right { left: 433px; }
  .section-banner { position: absolute; width: 230px; height: 51px; }
  .section-banner svg { position: absolute; inset: 0; }
  .section-banner h2 {
    position: absolute; left: 6px; top: 12px;
    font-size: 19px; font-weight: 700; color: #fff; font-style: normal;
  }
  .sub-tab {
    position: absolute; width: 210px; height: 42px; background: var(--paper);
    box-shadow: 3px 3px 4px rgba(0,0,0,0.18);
  }
  .sub-tab h3 {
    position: absolute; left: 8px; top: 10px;
    font-size: 15.5px; font-weight: 600; font-style: italic; color: var(--ink);
  }
  .tab-left { left: 27px; }
  .tab-right { left: 427px; }
  .page-number {
    position: absolute; right: 48px; top: 1160px;
    font-size: 16px; color: #444;
  }
</style>
</head>
<body>
<div class="page">
  <div class="edge-band"></div>

  <!-- Left column -->
  <p class="copy col-left" style="top:36px">For insurance and managed funds (except under the MDA service) recommendations, we will provide you with a Product Disclosure Statement. This contains information to help you understand the product being recommended.</p>
  <p class="copy col-left" style="top:153px">At all times you are able to contact us and ask questions about the advice and investments recommended. You can provide instructions to us in writing, via phone or via email/fax. Please note you are responsible for ensuring your instructions do actually reach us.</p>
  <p class="copy col-left" style="top:268px">We may provide further advice to you to keep your plan up to date with changes in your circumstances, changes in the law and changes in the economy and investments.</p>
  <p class="copy col-left" style="top:364px">The further advice we provide will be dependent on the Terms of Engagement you sign with us. It will be documented in a Record of Advice.</p>

  <div class="section-banner" style="left:30px; top:443px">
    <svg width="230" height="51" viewBox="0 0 230 51" aria-hidden="true">
      <rect width="230" height="51" fill="var(--brand-blue)"/>
      <polygon points="178,0 226,0 230,4 230,51" fill="var(--brand-navy)"/>
      <polygon points="184,0 226,0 230,4 230,44" fill="var(--brand-green)"/>
    </svg>
    <h2>Fees</h2>
  </div>

  <p class="copy col-left" style="top:517px">All fees are payable to Corvelle Advisory Pty Ltd as Trustee for Harlow Trust.</p>
  <p class="copy col-left" style="top:575px">Daniel Whitford is a beneficiary of Harlow Trust and shares in the profits of the business.</p>
  <p class="copy col-left" style="top:632px">Marcus Ellery and Owen Kessler are employees of Corvelle Advisory Pty Ltd as Trustee for Harlow Trust. They will be paid a salary and may receive a performance bonus which amongst other items will be based on the revenue they generate for the business.</p>
  <p class="copy col-left" style="top:749px">Your first meeting with us is complimentary and obligation free.</p>

  <div class="sub-tab tab-left" style="top:795px"><h3>Plan Preparation Fee</h3></div>
  <p class="copy col-left" style="top:846px">The Plan Preparation fee includes all meetings with you, the time we take to determine our advice and the production of the SoA.</p>
  <p class="copy col-left" style="top:921px">The Plan Preparation fee is based on the scope and complexity of advice provided to you. We will agree the fee with you at our first meeting or shortly after.</p>

  <!-- Right column -->
  <div class="sub-tab tab-right" style="top:25px"><h3>Plan Implementation Fee</h3></div>
  <p class="copy col-right" style="top:76px">If you decide to proceed with our advice we may charge a fee for the time we spend assisting you with implementation. We will let you know what the fee will be in the SoA.</p>

  <div class="sub-tab tab-right" style="top:158px"><h3>Ongoing Services Fees</h3></div>
  <p class="copy col-right" style="top:212px">Once your investments are established we may provide you with ongoing services.<br>Ongoing fees will depend on the services we provide to you. They may be a percentage of the transaction value, an agreed fixed fee or a percentage of your portfolio value.<br>The services and fees will be set out in the SoA or RoA that we provide to you.</p>

  <div class="section-banner" style="left:425px; top:385px">
    <svg width="230" height="51" viewBox="0 0 230 51" aria-hidden="true">
      <rect width="230" height="51" fill="var(--brand-blue)"/>
      <polygon points="178,0 226,0 230,4 230,51" fill="var(--brand-navy)"/>
      <polygon points="184,0 226,0 230,4 230,44" fill="var(--brand-green)"/>
    </svg>
    <h2>Commissions</h2>
  </div>

  <p class="copy col-right" style="top:461px">The Harlow Trust, Daniel Whitford, Marcus Ellery and Owen Kessler may receive commissions and other benefits from some product and service providers.</p>
  <p class="copy col-right" style="top:538px">The commission amount will vary depending on the product or service which is recommended. We will disclose the exact amount in the SoA or RoA.</p>

  <div class="sub-tab tab-right" style="top:603px"><h3>Insurance Commission</h3></div>
  <p class="copy col-right" style="top:654px">We may receive a one-off upfront commission when you take out an insurance policy we recommend.</p>
  <p class="copy col-right" style="top:711px">We may also receive a monthly commission payment for as long as you continue to hold the policy.</p>

  <div class="sub-tab tab-right" style="top:757px"><h3>Placement Commissions</h3></div>
  <p class="copy col-right" style="top:807px">We may receive a placement commission on capital raisings undertaken by companies. This includes initial public offerings and rights issues. These are one-off payments.</p>

  <div class="sub-tab tab-right" style="top:891px"><h3>Other Benefits</h3></div>
  <p class="copy col-right" style="top:943px">We may receive additional benefits by way of sponsorship of education seminars, conferences or training days. Details of any benefits received above $100 will be maintained on a register which is available to you on request.</p>

  <div class="page-number">Page 4 of 6</div>
</div>
</body>
</html>
```